Website update for Harborline Ledger Partners & Bookkeeping

Our website needs updating
www.harborlineledgerpartners.com
Here are some of our latest print pieces to use as a guide?
I have also attached our graphic identity guide which includes the Pantone colors

Target Market(s)

Insurance Agencies

Industry/Entity Type

Accounting

Number of Pages Required

5+ page

```html
<!DOCTYPE html>
<html lang="en">
<head>
<meta charset="utf-8">
<title>Harborline Ledger Partners &amp; Bookkeeping</title>
<link rel="stylesheet" href="https://fonts.googleapis.com/css2?family=Raleway:wght@300;400;600&family=Open+Sans:wght@400;600&display=swap">
<style>
:root{
  --teal:#1aaa9b;
  --teal-dark:#138f83;
  --teal-deep:#0e7c71;
  --teal-light:#b4eee7;
  --teal-pale:#dff8f5;
  --ink:#3a4a4a;
  --muted:#6b7777;
  --white:#ffffff;
}
*{margin:0;padding:0;box-sizing:border-box}
html,body{width:1200px;height:3680px;overflow:hidden}
body{font-family:"Open Sans",Arial,sans-serif;color:var(--ink);background:var(--white)}
.hero{position:relative;height:660px;background:linear-gradient(135deg,#f4f7f8 0%,#dfe6ea 45%,#c9d3d8 100%)}
.hero-photo{position:absolute;inset:0}
.nav{position:absolute;top:0;left:110px;width:980px;height:40px;background:rgba(255,255,255,.9);display:flex;justify-content:center;gap:6px;box-shadow:0 1px 4px rgba(0,0,0,.1)}
.nav a{font-family:"Raleway",sans-serif;font-size:15px;color:var(--teal-dark);text-decoration:none;padding:0 18px;line-height:40px}
.nav a.active{background:var(--teal);color:var(--white)}
.brand{position:absolute;top:90px;left:0;right:0;display:flex;justify-content:center;align-items:center;gap:16px}
.brand-mark{width:56px;height:56px;background:var(--teal)}
.brand-name{font-family:"Raleway",sans-serif;font-weight:600;font-size:34px;color:var(--teal-dark);max-width:460px;line-height:1.15}
.dots{position:absolute;bottom:22px;left:0;right:0;display:flex;justify-content:center;gap:16px}
.dots span{width:14px;height:14px;border-radius:50%;background:rgba(255,255,255,.8)}
.dots span.on{background:var(--teal)}
.about{height:412px;background:var(--teal);color:var(--white);text-align:center;padding-top:36px}
.about h2{font-family:"Raleway",sans-serif;font-weight:400;font-size:46px}
.about p{width:880px;margin:28px auto 0;font-size:15px;line-height:26px}
.btn{display:inline-block;margin-top:30px;border:2px solid var(--white);border-radius:22px;padding:8px 32px;font-size:16px;color:var(--white)}
.service{height:292px;display:flex;align-items:center;justify-content:center;gap:100px}
.service.alt{background:linear-gradient(180deg,var(--teal-light),var(--teal-pale))}
.service .visual{width:380px;height:220px;border-radius:4px}
.service .copy{width:420px}
.service h3{font-family:"Raleway",sans-serif;font-weight:400;font-size:34px;line-height:40px;color:var(--teal-dark);text-transform:uppercase}
.service p{margin-top:14px;font-size:14px;line-height:22px;color:var(--muted)}
.why{height:344px;background:var(--teal);color:var(--white);text-align:center;padding-top:40px}
.why h2{font-family:"Raleway",sans-serif;font-weight:400;font-size:46px}
.why-list{display:flex;justify-content:center;gap:110px;margin-top:44px}
.why-item{width:170px}
.why-icon{width:96px;height:96px;border-radius:50%;border:3px solid var(--white);margin:0 auto;display:flex;align-items:center;justify-content:center}
.why-item span{display:block;margin-top:16px;font-size:18px}
.footer{height:220px;background:var(--teal-deep);color:var(--white);padding:36px 110px 0}
.footer-top{display:flex;justify-content:space-between;align-items:center;border-bottom:1px solid rgba(255,255,255,.3);padding-bottom:28px}
.links{display:flex;gap:46px;font-size:15px;letter-spacing:1px}
.links .first{border:2px solid var(--white);border-radius:18px;padding:4px 18px;margin:-6px 0}
.social{display:flex;gap:16px}
.social span{width:40px;height:40px;border-radius:50%;border:2px solid var(--white)}
.contact{display:flex;justify-content:space-between;margin-top:22px;font-size:15px}
.contact div{display:flex;align-items:center;gap:10px}
.copyright{text-align:center;margin-top:24px;font-size:13px;opacity:.85}
</style>
</head>
<body>
<header class="hero">
  <div class="hero-photo" role="img" aria-label="Photo of a hand using a calculator on a bright desk"></div>
  <nav class="nav">
    <a class="active">Home</a><a>About Us</a><a>Company</a><a>Our Services</a><a>How it Works</a><a>Resources</a><a>Contact Us</a><a>Blog</a>
  </nav>
  <div class="brand"><span class="brand-mark"></span><span class="brand-name">Harborline Ledger Partners &amp; Bookkeeping</span></div>
  <div class="dots"><span class="on"></span><span></span><span></span></div>
</header>

<section class="about">
  <h2>About Us</h2>
  <p>Welcome to the HLPB. After working in house at agencies for many years, Dana Whitfield formed HLPB in 2011 to help independent Insurance Agencies manage their accounting and bookkeeping. HLPB currently has 15 staff members working in our Connecticut office cross-trained in all aspects of agency accounting. We have just added the capacity for 8 additional staff members. Call us, we'll be ready to meet your unique needs.</p>
  <span class="btn">Know More</span>
</section>

<section class="service">
  <div class="visual" role="img" aria-label="Illustration of piggy banks with falling coins" style="background:linear-gradient(135deg,#f6c9d3,#e89aae)"></div>
  <div class="copy"><h3>Record Direct Bill Commission</h3><p>Lorem Ipsum is simply dummy text of the printing and typesetting industry. Lorem Ipsum has been the industry's standard dummy text ever since the 1500s, when an unknown printer took a galley of type and scrambled it to make a type specimen book.</p></div>
</section>
<section class="service alt">
  <div class="copy"><h3>Reconcile &amp; Pay Agency Bill Premiums</h3><p>Lorem Ipsum is simply dummy text of the printing and typesetting industry. Lorem Ipsum has been the industry's standard dummy text ever since the 1500s, when an unknown printer took a galley of type and scrambled it to make a type specimen book.</p></div>
  <div class="visual" role="img" aria-label="Photo of a hand holding a fan of banknotes" style="background:linear-gradient(135deg,#c9d6b4,#8fa477)"></div>
</section>
<section class="service">
  <div class="visual" role="img" aria-label="Illustration of a ledger notebook, calculator and pen" style="background:linear-gradient(135deg,#d9c4a8,#7a6a5a)"></div>
  <div class="copy"><h3>Reconcile General Ledger Accounts</h3><p>Lorem Ipsum is simply dummy text of the printing and typesetting industry. Lorem Ipsum has been the industry's standard dummy text ever since the 1500s, when an unknown printer took a galley of type and scrambled it to make a type specimen book.</p></div>
</section>
<section class="service alt">
  <div class="copy"><h3>Prepare &amp; Interpret Financial Statements</h3><p>Lorem Ipsum is simply dummy text of the printing and typesetting industry. Lorem Ipsum has been the industry's standard dummy text ever since the 1500s, when an unknown printer took a galley of type and scrambled it to make a type specimen book.</p></div>
  <div class="visual" role="img" aria-label="Illustration of a green bar chart with a globe" style="background:linear-gradient(135deg,#d6ecd2,#7bbf74)"></div>
</section>
<section class="service">
  <div class="visual" role="img" aria-label="Illustration of an invoice sheet with stacks of coins" style="background:linear-gradient(135deg,#eef0f4,#e4b64a)"></div>
  <div class="copy"><h3>Pay Vendor Invoives</h3><p>Lorem Ipsum is simply dummy text of the printing and typesetting industry. Lorem Ipsum has been the industry's standard dummy text ever since the 1500s, when an unknown printer took a galley of type and scrambled it to make a type specimen book.</p></div>
</section>
<section class="service alt">
  <div class="copy"><h3>Reconcile Customer Accounts Receivable</h3><p>Lorem Ipsum is simply dummy text of the printing and typesetting industry. Lorem Ipsum has been the industry's standard dummy text ever since the 1500s, when an unknown printer took a galley of type and scrambled it to make a type specimen book.</p></div>
  <div class="visual" role="img" aria-label="Photo of a pen resting on a signed document" style="background:linear-gradient(135deg,#f2e6cf,#b48a5a)"></div>
</section>
<section class="service">
  <div class="visual" role="img" aria-label="Illustration of green payroll lettering with office figures" style="background:linear-gradient(135deg,#e4f0d8,#5aa84a)"></div>
  <div class="copy"><h3>Process Payroll</h3><p>Lorem Ipsum is simply dummy text of the printing and typesetting industry. Lorem Ipsum has been the industry's standard dummy text ever since the 1500s, when an unknown printer took a galley of type and scrambled it to make a type specimen book.</p></div>
</section>

<section class="why">
  <h2>Why it Works</h2>
  <div class="why-list">
    <div class="why-item"><div class="why-icon"><svg width="50" height="40" viewBox="0 0 50 40" fill="#fff"><circle cx="25" cy="11" r="8"/><rect x="13" y="22" width="24" height="16" rx="8"/><circle cx="9" cy="15" r="5"/><circle cx="41" cy="15" r="5"/></svg></div><span>Educated &amp; Trained Staff</span></div>
    <div class="why-item"><div class="why-icon"><svg width="44" height="44" viewBox="0 0 44 44" fill="none" stroke="#fff" stroke-width="4"><circle cx="22" cy="22" r="18"/><path d="M13 22l6 6 12-12"/></svg></div><span>Quality Control</span></div>
    <div class="why-item"><div class="why-icon"><svg width="48" height="40" viewBox="0 0 48 40" fill="none" stroke="#fff" stroke-width="4"><path d="M4 12h34M30 4l8 8-8 8M44 28H10M18 20l-8 8 8 8"/></svg></div><span>Separation of Duties</span></div>
    <div class="why-item"><div class="why-icon"><svg width="36" height="44" viewBox="0 0 36 44" fill="#fff"><path d="M9 18v-6a9 9 0 0118 0v6" fill="none" stroke="#fff" stroke-width="4"/><rect x="3" y="18" width="30" height="24" rx="3"/></svg></div><span>Data Security</span></div>
  </div>
</section>

<footer class="footer">
  <div class="footer-top">
    <div class="links"><span class="first">TERMS</span><span>CONDITIONS</span><span>DISCLAIMER</span><span>FAQS</span></div>
    <div class="social"><span></span><span></span><span></span></div>
  </div>
  <div class="contact">
    <div><svg width="16" height="22" viewBox="0 0 16 22" fill="#fff"><path d="M8 0a8 8 0 00-8 8c0 6 8 14 8 14s8-8 8-14a8 8 0 00-8-8zm0 11a3 3 0 110-6 3 3 0 010 6z"/></svg>42 Quayside Ave, Portmere, CT 06010</div>
    <div><svg width="18" height="18" viewBox="0 0 24 24" fill="#fff"><path d="M6.6 10.8a15 15 0 006.6 6.6l2.2-2.2a1 1 0 011-.25 11 11 0 003.6.6 1 1 0 011 1V20a1 1 0 01-1 1A17 17 0 013 4a1 1 0 011-1h3.5a1 1 0 011 1 11 11 0 00.6 3.6 1 1 0 01-.25 1z"/></svg>555-014-2290</div>
    <div><svg width="20" height="16" viewBox="0 0 20 16" fill="none" stroke="#fff" stroke-width="2"><rect x="1" y="1" width="18" height="14"/><path d="M1 1l9 8 9-8"/></svg>info@harborlineledgerpartners.com</div>
  </div>
  <p class="copyright">&copy; Harborline Ledger Partners &amp; Bookkeeping - 2015. All Rights Reserved</p>
</footer>
</body>
</html>
```